Website design and coding for new consultancy company

I need to have a full website designed for a new consultancy business I'm trying to establish. It's called BrightPath consult. I need an English version to begin with, and then there should be a Danish version as well, but I'll translate that myself. Just be aware that I need two language versions. The consultancy field that I'm targeting is Leadership - and specialist development. I offer to facilitate corporate academies for global companies as well as specific workshops within leadership- or team development, strategy sessions, personal coaching and facilitation of D&I (Diversity and inclusion) workshops. BTW my logo is not in high resolution - I need that as well.

Target Market(s)

Larger companies that has a need for developing their inhouse leadership capabilities or that wants to develop their specialists to take on more responsibility.

Industry/Entity Type

Consultancy business

Coding

Coded - Design and coding required

Number of Pages Required

5+ page

Requirements
Must have
• Introduction site with a catch phrase. Book a meeting. Services that's beeing offered. Blog site with white papers etc. Language toggle (Danish/English). Cases/testimonials. About site. Contact site.

```html
<!DOCTYPE html>
<html lang="en">
<head>
<meta charset="utf-8">
<title>BrightPath consult – Leadership & Specialist Development</title>
<link href="https://fonts.googleapis.com/css2?family=Oswald:wght@400;500;600;700&family=Open+Sans:wght@400;600;700&display=swap" rel="stylesheet">
<style>
:root{
  --blue:#1f6fc9;
  --blue-dark:#1558a6;
  --navy:#1b2a44;
  --ink:#1d1d1f;
  --grey:#5a5f66;
  --light:#eef0f3;
  --line:#d6dbe2;
  --footer:#141414;
  --white:#ffffff;
}
*{box-sizing:border-box;margin:0;padding:0}
html,body{width:1200px;height:4668px;overflow:hidden}
body{font-family:"Open Sans",Arial,sans-serif;color:var(--ink);background:var(--white);position:relative}
h1,h2,h3,h4,.brand,.nav a,.btn{font-family:"Oswald","Arial Narrow",sans-serif}
.sec{position:absolute;left:0;width:1200px;overflow:hidden}
.btn{display:inline-block;background:var(--blue);color:var(--white);font-size:14px;font-weight:500;letter-spacing:.5px;padding:8px 18px;text-transform:uppercase}
.hl{color:var(--blue)}
p{font-size:15px;line-height:1.6;color:var(--grey)}

/* header */
.header{top:0;height:72px;background:var(--white);display:flex;align-items:center;padding:0 150px;z-index:3}
.brand{display:flex;align-items:center;gap:12px;font-size:30px;font-weight:700;color:var(--navy);letter-spacing:1px}
.brand-sq{width:30px;height:30px;background:var(--blue)}
.nav{margin-left:auto;display:flex;align-items:center;gap:34px}
.nav a{font-size:14px;color:var(--navy);text-decoration:none;letter-spacing:.5px;position:relative}
.nav a.active{color:var(--blue)}
.nav a.active::after{content:"";position:absolute;left:0;right:0;bottom:-6px;height:2px;background:var(--blue)}
.nav .btn{padding:9px 22px}

/* hero */
.hero{top:72px;height:596px;background:linear-gradient(100deg,#f4f5f7 0%,#e3e6ea 35%,#b9bfc7 60%,#8b96a3 100%)}
.hero-photo{position:absolute;inset:0;background:linear-gradient(90deg,rgba(255,255,255,.9) 0%,rgba(255,255,255,.55) 38%,rgba(140,150,165,.2) 60%,rgba(60,75,95,.35) 100%)}
.hero-copy{position:absolute;left:150px;top:40px;width:520px}
.hero h1{font-size:48px;line-height:1.1;font-weight:600;color:var(--navy);text-transform:uppercase}
.hero p{margin-top:22px;color:var(--ink);font-size:15px;width:420px}
.hero .btn{margin-top:24px}

/* services */
.services{top:668px;height:1000px;background:var(--white)}
.sec-title{text-align:center;font-size:40px;font-weight:600;color:var(--ink)}
.services .sec-title{margin-top:60px}
.cards{position:absolute;left:148px;top:188px;width:904px;display:grid;grid-template-columns:repeat(3,292px);gap:24px 14px}
.card{height:364px;border:1px solid var(--line);background:var(--white);text-align:center;padding:34px 30px 0;box-shadow:0 2px 6px rgba(0,0,0,.05)}
.card svg{width:110px;height:96px}
.card h3{font-size:17px;font-weight:600;margin-top:16px;text-transform:uppercase;line-height:1.25}
.card p{font-size:13px;line-height:1.5;margin-top:8px}
.card .btn{margin-top:14px;font-size:12px;padding:6px 14px}
.card.dark{background:linear-gradient(160deg,#3a3f47,#1e2228);border:none}
.card.dark h3{color:var(--white)}
.card.dark p{color:#d6d9de}
.card.blue{background:linear-gradient(160deg,#2a7bd6,#1a5fb0);border:none;display:flex;align-items:center;justify-content:center;padding:0}
.btn-outline{font-family:"Oswald",sans-serif;color:var(--white);border:2px solid var(--white);padding:12px 22px;font-size:16px;letter-spacing:.5px}
.deco{position:absolute}

/* journeys */
.journeys{top:1668px;height:512px;background:var(--light)}
.journeys .photo{position:absolute;left:148px;top:28px;width:380px;height:484px;background:linear-gradient(160deg,#dfe3e8,#b8c2cf 60%,#7d8da2)}
.journeys .copy{position:absolute;left:568px;top:40px;width:480px}
.journeys h2{font-size:34px;line-height:1.2;font-weight:600;text-transform:uppercase}
.journeys p{margin-top:14px;font-size:13px}
.stats{display:flex;gap:40px;margin-top:22px}
.stat b{display:block;font-family:"Oswald",sans-serif;font-size:32px;color:var(--blue);font-weight:500}
.stat span{display:block;font-size:11px;font-weight:700;color:var(--ink);text-transform:uppercase;width:120px;line-height:1.3}
.journeys .btn{margin-top:22px;font-size:12px}

/* practice */
.practice{top:2180px;height:620px;background:var(--blue)}
.practice .copy{position:absolute;left:148px;top:80px;width:400px}
.practice h2{font-size:36px;line-height:1.2;font-weight:600;color:var(--white);text-transform:uppercase}
.practice p{color:#e3edf9;font-size:13px;margin-top:26px}
.practice .btn{background:var(--white);color:var(--navy);margin-top:22px;font-size:12px}
.practice svg{position:absolute;left:580px;top:40px}

/* untapped */
.untapped{top:2800px;height:420px;background:var(--white)}
.untapped svg{position:absolute;left:0;top:-20px}
.untapped .copy{position:absolute;left:660px;top:70px;width:420px}
.untapped h2{font-size:34px;line-height:1.2;font-weight:600;text-transform:uppercase}
.untapped p{margin-top:18px;font-size:13px}
.untapped .btn{margin-top:22px;font-size:12px}

/* testimonials */
.testimonials{top:3220px;height:640px;background:var(--light)}
.testimonials h2{position:absolute;left:148px;top:56px;font-size:36px;font-weight:600;text-transform:uppercase}
.arrows{position:absolute;right:150px;top:62px;display:flex;gap:10px}
.arrows span{width:36px;height:36px;border-radius:50%;display:flex;align-items:center;justify-content:center;background:#9aa0a8}
.arrows span.on{background:var(--white);border:2px solid var(--blue)}
.tcards{position:absolute;left:148px;top:160px;display:flex;gap:24px}
.tcard{width:285px;height:410px;background:var(--white);padding:30px 28px;box-shadow:0 2px 8px rgba(0,0,0,.06)}
.quote{font-family:Georgia,serif;font-size:56px;line-height:.6;color:var(--blue)}
.tcard p{font-size:13px;margin-top:18px;color:var(--grey)}
.person{display:flex;align-items:center;gap:12px;margin-top:22px}
.avatar{width:40px;height:40px;border-radius:50%;background:var(--navy);color:var(--white);font-size:13px;font-weight:700;display:flex;align-items:center;justify-content:center}
.person b{display:block;font-size:13px;text-transform:uppercase}
.person span{font-size:12px;color:var(--grey)}

/* contact */
.contact{top:3860px;height:560px;background:var(--blue)}
.contact .diag{position:absolute;left:0;top:0}
.contact h2{position:absolute;left:148px;top:54px;font-size:36px;font-weight:600;color:var(--white);text-transform:uppercase}
.form{position:absolute;left:148px;top:144px;width:484px}
.field{height:44px;background:var(--white);margin-bottom:16px;padding:0 14px;display:flex;align-items:center;font-size:12px;font-weight:600;color:#555;text-transform:uppercase}
.field.msg{height:130px;align-items:flex-start;padding-top:14px}
.submit{height:54px;background:#111;color:var(--white);font-family:"Oswald",sans-serif;font-size:20px;display:flex;align-items:center;justify-content:center;letter-spacing:1px}
.contact .person-photo{position:absolute;left:610px;top:0}

/* footer */
.footer{top:4420px;height:248px;background:var(--footer);color:#cfd2d6}
.footer .brand{color:var(--white);position:absolute;left:148px;top:40px;font-size:34px}
.footer .about{position:absolute;left:148px;top:100px;width:300px;font-size:12px;color:#aeb2b8}
.fcol{position:absolute;top:40px}
.fcol h4{font-size:15px;font-weight:500;color:var(--blue);text-transform:uppercase;margin-bottom:12px}
.fcol li{list-style:none;font-size:12px;margin-bottom:8px;display:flex;gap:10px;align-items:flex-start}
.social{display:flex;gap:8px}
.social span{width:26px;height:26px;border-radius:50%;background:var(--white)}
.fcol .btn{margin-top:16px;font-size:12px;padding:8px 20px}
.copy-bar{position:absolute;left:0;right:0;bottom:0;height:38px;border-top:1px solid #2a2a2a;text-align:center;line-height:38px;font-size:11px;color:#9ca0a6}
</style>
</head>
<body>

<header class="sec header">
  <div class="brand"><span class="brand-sq"></span>BRIGHTPATH</div>
  <nav class="nav">
    <a class="active" href="#">HOME</a>
    <a href="#">ABOUT US</a>
    <a href="#">WHAT WE DO</a>
    <a href="#">RESOURCES</a>
    <a href="#">CONTACT US</a>
    <a class="btn" href="#">LETS TALK &nbsp;›</a>
  </nav>
</header>

<section class="sec hero">
  <div class="hero-photo" role="img" aria-label="Photo of a leader presenting to a team seated around a meeting table in a bright office"></div>
  <div class="hero-copy">
    <h1>Shaping stronger leaders. <span class="hl">Building thriving teams.</span></h1>
    <p>We help organizations unlock their <b>leadership potential and create sustainable growth</b> through tailored academies, workshops, and coaching.</p>
    <a class="btn" href="#">CONTACT US &nbsp;›</a>
  </div>
</section>

<section class="sec services">
  <h2 class="sec-title">OUR <span class="hl">SERVICES</span></h2>
  <svg class="deco" style="left:128px;top:168px" width="40" height="30"><g stroke="#1f6fc9" stroke-width="2"><line x1="4" y1="4" x2="14" y2="14"/><line x1="20" y1="2" x2="20" y2="14"/></g></svg>
  <svg class="deco" style="left:1034px;top:168px" width="40" height="30"><g stroke="#1f6fc9" stroke-width="2"><line x1="20" y1="2" x2="20" y2="14"/><line x1="36" y1="4" x2="26" y2="14"/></g></svg>
  <div class="cards">
    <div class="card">
      <svg viewBox="0 0 110 96"><path d="M55 4 L106 92 H4 Z" fill="none" stroke="#1f6fc9" stroke-width="3"/><circle cx="55" cy="52" r="9" fill="#1b2a44"/><rect x="40" y="66" width="30" height="14" fill="#1f6fc9"/></svg>
      <h3>Corporate Academies</h3>
      <p>We design and facilitate customized academies for global companies, equipping leaders and specialists with the tools they need for long-term success.</p>
      <a class="btn" href="#">READ MORE</a>
    </div>
    <div class="card dark" role="img" aria-label="Photo of a team workshop behind the card text">
      <svg viewBox="0 0 110 96"><path d="M55 4 L106 92 H4 Z" fill="none" stroke="#ffffff" stroke-width="3"/><circle cx="42" cy="56" r="7" fill="#fff"/><circle cx="68" cy="56" r="7" fill="#fff"/><rect x="34" y="68" width="42" height="12" fill="#fff"/></svg>
      <h3>Leadership &amp; Team Development Workshops</h3>
      <p>Interactive workshops to strengthen leadership skills, improve collaboration, and boost team performance.</p>
      <a class="btn" href="#">READ MORE</a>
    </div>
    <div class="card">
      <svg viewBox="0 0 110 96"><path d="M55 4 L106 92 H4 Z" fill="none" stroke="#1f6fc9" stroke-width="3"/><rect x="38" y="44" width="34" height="24" fill="none" stroke="#1b2a44" stroke-width="3"/><line x1="44" y1="62" x2="66" y2="50" stroke="#1f6fc9" stroke-width="3"/></svg>
      <h3>Strategy Facilitation</h3>
      <p>Expertly guided strategy sessions align leadership teams, sharpen decision-making, and set a clear direction for the future.</p>
      <a class="btn" href="#">READ MORE</a>
    </div>
    <div class="card">
      <svg viewBox="0 0 110 96"><path d="M55 4 L106 92 H4 Z" fill="none" stroke="#1f6fc9" stroke-width="3"/><circle cx="46" cy="52" r="8" fill="#1b2a44"/><circle cx="66" cy="56" r="6" fill="#1f6fc9"/><rect x="36" y="66" width="40" height="12" fill="#1b2a44"/></svg>
      <h3>Personal Coaching</h3>
      <p>Individual coaching that empowers leaders and specialists to grow their impact, performance, and confidence in achieving professional goals.</p>
      <a class="btn" href="#">READ MORE</a>
    </div>
    <div class="card">
      <svg viewBox="0 0 110 96"><path d="M55 4 L106 92 H4 Z" fill="none" stroke="#1f6fc9" stroke-width="3"/><circle cx="40" cy="58" r="6" fill="#1b2a44"/><circle cx="55" cy="52" r="6" fill="#1f6fc9"/><circle cx="70" cy="58" r="6" fill="#1b2a44"/><rect x="32" y="68" width="46" height="10" fill="#1f6fc9"/></svg>
      <h3>Diversity &amp; Inclusion Workshops</h3>
      <p>Inclusive workshops that value diverse perspectives, foster equitable workplace culture, and strengthen organizational collaboration and innovation.</p>
      <a class="btn" href="#">READ MORE</a>
    </div>
    <div class="card blue" role="img" aria-label="Blue-tinted photo of colleagues collaborating">
      <span class="btn-outline">VIEW ALL SERVICES</span>
    </div>
  </div>
</section>

<section class="sec journeys">
  <div class="photo" role="img" aria-label="Portrait photo of a smiling consultant in a suit"></div>
  <div class="copy">
    <h2>Innovative learning journeys to meet your most pressing <span class="hl">leadership challenges</span></h2>
    <p>Our programs combine practical tools, reflection and peer learning so that leaders build lasting habits. Every journey is tailored to your strategy, culture and people, and designed to create measurable change in how teams lead, decide and collaborate across borders and functions every day.</p>
    <div class="stats">
      <div class="stat"><b>96%</b><span>Overall satisfaction</span></div>
      <div class="stat"><b>85%</b><span>Of executives benefited from coaching</span></div>
      <div class="stat"><b>82%</b><span>Of specialists take on more responsibility</span></div>
    </div>
    <a class="btn" href="#">READ MORE</a>
  </div>
</section>

<section class="sec practice">
  <div class="copy">
    <h2>Leadership as a practice: developing skills for lasting impact</h2>
    <p>Leadership is not a title but a daily practice. We help managers build the skills to coach, give feedback and lead change with confidence. Through hands-on sessions and real cases, your leaders learn to turn insight into action and keep growing long after the program ends, creating lasting impact.</p>
    <a class="btn" href="#">READ MORE</a>
  </div>
  <svg width="520" height="540" viewBox="0 0 520 540">
    <path d="M260 20 L510 520 H10 Z" fill="#ffffff"/>
    <path d="M260 46 L486 506 H34 Z" fill="#c8ccd2" role="img" aria-label="Photo of a workshop with participants seated around tables"/>
  </svg>
</section>

<section class="sec untapped">
  <svg width="620" height="460" viewBox="0 0 620 460">
    <path d="M0 20 L520 20 L300 440 L0 440 Z" fill="#1f6fc9"/>
    <path d="M320 40 L580 440 H60 Z" fill="#ffffff"/>
    <path d="M320 70 L552 428 H88 Z" fill="#c4ccd6" role="img" aria-label="Photo of a smiling specialist holding a laptop in a modern office"/>
  </svg>
  <div class="copy">
    <h2>The untapped potential of <span class="hl">specialists in driving</span> strategy</h2>
    <p>Specialists hold deep knowledge that often goes unused in strategic decisions. We help organizations develop their experts into trusted voices who influence direction, lead projects and take on more responsibility while staying close to the craft they love and excel at.</p>
    <a class="btn" href="#">READ MORE</a>
  </div>
</section>

<section class="sec testimonials">
  <h2>Testimonials</h2>
  <div class="arrows">
    <span><svg width="14" height="14"><path d="M10 2 L4 7 L10 12" fill="none" stroke="#fff" stroke-width="2"/></svg></span>
    <span class="on"><svg width="14" height="14"><path d="M4 2 L10 7 L4 12" fill="none" stroke="#1f6fc9" stroke-width="2"/></svg></span>
  </div>
  <div class="tcards">
    <div class="tcard">
      <div class="quote">“</div>
      <p>The academy gave our managers a shared language for leadership. We saw stronger collaboration within weeks, and our teams now handle change with far more confidence. The facilitation was engaging, practical and perfectly tailored to our culture and global setup.</p>
      <div class="person"><div class="avatar">JB</div><div><b>Jonas Berg</b><span>USA</span></div></div>
    </div>
    <div class="tcard">
      <div class="quote">“</div>
      <p>Our specialists grew into real leaders. The coaching helped them step up, own decisions and guide projects across departments. The program was focused, personal and built around our actual challenges, which made the results lasting and easy to see.</p>
      <div class="person"><div class="avatar">JB</div><div><b>Jonas Berg</b><span>USA</span></div></div>
    </div>
    <div class="tcard">
      <div class="quote">“</div>
      <p>The strategy session brought our leadership team into alignment. Clear structure, honest dialogue and skilled facilitation helped us agree on priorities we had debated for months. We left with a plan everyone owned and the energy to carry it out.</p>
      <div class="person"><div class="avatar">JB</div><div><b>Jonas Berg</b><span>USA</span></div></div>
    </div>
  </div>
</section>

<section class="sec contact">
  <svg class="diag" width="1200" height="560"><path d="M820 0 L1200 0 L1200 560 L1000 560 Z" fill="#ffffff"/></svg>
  <h2>Contact us</h2>
  <div class="form">
    <div class="field">Full name</div>
    <div class="field">Email ID</div>
    <div class="field">Phone</div>
    <div class="field msg">Message</div>
    <div class="submit">SUBMIT</div>
  </div>
  <svg class="person-photo" width="480" height="560"><path d="M90 40 H400 V560 H60 Z" fill="#9fb0c6" opacity=".75" role="img" aria-label="Photo of a smiling consultant holding a laptop"/></svg>
</section>

<footer class="sec footer">
  <div class="brand"><span class="brand-sq"></span>BRIGHTPATH</div>
  <p class="about">BrightPath consult supports global companies in developing leaders and specialists through academies, workshops, strategy sessions and coaching that create lasting impact.</p>
  <div class="fcol" style="left:510px">
    <h4>Contact us</h4>
    <ul>
      <li><svg width="12" height="14"><path d="M6 1a4 4 0 0 1 4 4c0 3-4 8-4 8S2 8 2 5a4 4 0 0 1 4-4z" fill="#fff"/></svg>Lindevej 12<br>8000 Aarhus, Denmark</li>
      <li><svg width="12" height="14"><path d="M2 2h3l1 3-2 1a7 7 0 0 0 4 4l1-2 3 1v3a1 1 0 0 1-1 1A11 11 0 0 1 1 3a1 1 0 0 1 1-1z" fill="#fff"/></svg>+45 3100 4477</li>
      <li><svg width="12" height="14"><rect x="1" y="3" width="11" height="8" fill="#fff"/><path d="M1 3l5.5 4L12 3" fill="none" stroke="#141414"/></svg>info@brightpathconsult.dk</li>
    </ul>
  </div>
  <div class="fcol" style="left:760px">
    <h4>Menu</h4>
    <ul><li>Home</li><li>About us</li><li>What We Do</li><li>Resources</li><li>Contact Us</li></ul>
  </div>
  <div class="fcol" style="left:920px">
    <h4>Follow us</h4>
    <div class="social"><span></span><span></span><span></span><span></span><span></span></div>
    <a class="btn" href="#">LETS TALK &nbsp;›</a>
  </div>
  <div class="copy-bar">Copyright © 2025 All Rights Reserved</div>
</footer>

</body>
</html>
```